Young, dynamic furniture company needs a new business card design

We require a new business card design for our modern furniture company which supplies furniture and appliances to the property and development market.
Oakridge Interiors has become one of the leading furniture & appliance suppliers to the property market withing London. With over 10 years experience, we have increased our business to supply not only private landlords and managing agents, but also property developers, housing associations and local councils.
We offer not only a complete range of furniture which includes beds, wardrobes, dining sets and sofas, but also a high quality, full delivery and assembly service to help you with all our furnishing needs.

Target Market(s)

Private landlords, estate agents, letting agents, property management companies

Industry/Entity Type

Business

Contact Information for Business Card

Name,
Title,
Address,
Mobile,
Telephone,
Fax, Website, email address

Font styles to use
Sans Serif

Colors
3176b5
0555a3
85abd2
cfdeed

Requirements
Must have
• All the above information for each of our staff, along with our logo

```html
<!DOCTYPE html>
<html lang="en">
<head>
<meta charset="utf-8">
<title>Oakridge Interiors – Business Card</title>
<link rel="stylesheet" href="https://fonts.googleapis.com/css2?family=Open+Sans:wght@400;600;700&display=swap">
<style>
  :root {
    --page-bg: #d8d4ce;
    --card-top-a: #f3f6f9;
    --card-top-b: #dfe6ee;
    --navy: #1f2f5c;
    --navy-light: #3a4f86;
    --brand-blue: #0555a3;
    --brand-blue-mid: #3176b5;
    --dark-a: #26272b;
    --dark-b: #0e0e10;
    --text-dark: #1b1f2a;
    --text-light: #e6e6e6;
    --text-soft: #cfcac2;
    --text-tan: #a8926f;
  }
  * { margin: 0; padding: 0; box-sizing: border-box; }
  html, body {
    width: 1200px; height: 969px; overflow: hidden;
    background: var(--page-bg);
    font-family: "Open Sans", Arial, sans-serif;
  }
  .card {
    position: absolute; left: 100px; top: 201px;
    width: 1000px; height: 567px; overflow: hidden;
    background: linear-gradient(160deg, var(--card-top-a), var(--card-top-b));
    box-shadow: 0 18px 40px rgba(0,0,0,.25);
  }
  .card-shapes { position: absolute; inset: 0; }
  .brand {
    position: absolute; left: 610px; top: 60px; width: 345px; text-align: center;
  }
  .brand-square {
    width: 110px; height: 110px; margin: 20px auto 28px;
    background: var(--brand-blue);
  }
  .brand-name {
    font-size: 27px; font-weight: 600; color: var(--text-dark);
    letter-spacing: .5px; text-transform: uppercase; white-space: nowrap;
  }
  .brand-tagline {
    font-size: 13px; font-weight: 700; color: var(--text-dark);
    letter-spacing: .3px; text-transform: uppercase; margin-top: 2px;
  }
  .person { position: absolute; left: 58px; top: 270px; color: var(--text-light); }
  .person-name { font-size: 33px; font-weight: 600; letter-spacing: 1px; line-height: 1.1; }
  .person-title { font-size: 25px; letter-spacing: 1px; margin-top: 4px; color: #cdd2de; }
  .contact-list { position: absolute; left: 70px; top: 392px; list-style: none; }
  .contact-list li {
    display: flex; align-items: center; height: 38.5px;
    font-size: 25px; color: var(--text-soft); letter-spacing: .5px;
  }
  .contact-list svg { width: 26px; height: 26px; margin-right: 22px; fill: var(--text-soft); }
  .address {
    position: absolute; right: 67px; top: 436px; text-align: right;
    font-size: 25px; color: var(--text-tan); line-height: 36px; letter-spacing: .5px;
  }
  .address .web { letter-spacing: 4px; }
</style>
</head>
<body>
  <div class="card">
    <svg class="card-shapes" width="1000" height="567" viewBox="0 0 1000 567">
      <defs>
        <linearGradient id="darkBand" x1="0" y1="0" x2="0" y2="1">
          <stop offset="0" stop-color="var(--dark-a)"/>
          <stop offset="1" stop-color="var(--dark-b)"/>
        </linearGradient>
        <linearGradient id="navyTab" x1="0" y1="0" x2="1" y2="0">
          <stop offset="0" stop-color="var(--navy-light)"/>
          <stop offset="1" stop-color="var(--navy)"/>
        </linearGradient>
        <linearGradient id="blueStripe" x1="0" y1="0" x2="0" y2="1">
          <stop offset="0" stop-color="var(--brand-blue-mid)"/>
          <stop offset="1" stop-color="var(--brand-blue)"/>
        </linearGradient>
      </defs>
      <rect x="0" y="373" width="1000" height="194" fill="url(#darkBand)"/>
      <polygon points="436,342 1000,342 1000,373 455,373" fill="url(#blueStripe)"/>
      <polygon points="0,255 392,255 455,373 0,373" fill="url(#navyTab)"/>
      <line x1="392" y1="255" x2="455" y2="373" stroke="#ffffff" stroke-width="3"/>
    </svg>

    <div class="brand">
      <div class="brand-square"></div>
      <div class="brand-name">Oakridge Interiors</div>
      <div class="brand-tagline">Trade Furniture Solutions</div>
    </div>

    <div class="person">
      <div class="person-name">DANIEL HARTLEY</div>
      <div class="person-title">PRESIDENT</div>
    </div>

    <ul class="contact-list">
      <li>
        <svg viewBox="0 0 24 24" aria-hidden="true"><path d="M3 8c0-2 4-4 9-4s9 2 9 4v2h-5V8H8v2H3z"/><rect x="5" y="11" width="14" height="9" rx="1"/></svg>
        512 7390 4418
      </li>
      <li>
        <svg viewBox="0 0 24 24" aria-hidden="true"><path d="M7 2h10a1 1 0 0 1 1 1v18a1 1 0 0 1-1 1H7a1 1 0 0 1-1-1V3a1 1 0 0 1 1-1zm1 3v13h8V5z"/></svg>
        847 2619 3370
      </li>
      <li>
        <svg viewBox="0 0 24 24" aria-hidden="true"><rect x="7" y="3" width="10" height="6"/><rect x="3" y="10" width="18" height="9" rx="1"/><rect x="7" y="17" width="10" height="4"/></svg>
        833 5104 2687
      </li>
      <li>
        <svg viewBox="0 0 24 24" aria-hidden="true"><path d="M3 6h18v12H3z" opacity=".9"/><path d="M3 6l9 7 9-7" fill="none" stroke="#1a1a1d" stroke-width="1.6"/></svg>
        dan@oakridge.com
      </li>
    </ul>

    <div class="address">
      <div>1270 Linden Avenue</div>
      <div>Maple Grove, NY 11020</div>
      <div class="web">www.oakridge.com</div>
    </div>
  </div>
</body>
</html>
```